wine label for ultra premium vineyard in Bendigo, Central Otago, New Zealand

"WREN" is our new wine brand, with grapes grown in our spectacular "ter Hoeven" vineyard. The small, elevated vineyard overlooks a river valley and snowy mountains. We would like a highly elegant label for our 2018 pinot noir wine, which highlights the quality of wine and our very special vineyard location. "WREN" has to be prominent, with secondary emphasis on "ter Hoeven vineyard" and "Bendigo, Central Otago". A stylized WREN logo (bird) could be a useful design device instead of the commonly seen illustrated mountain landscape (which is quite common for our local wines). Label size 90 high, 110 wide. Please use a pinot noir / burgundy bottle. See here for vineyard pics, and also below pics for other local wine labels and pics for inspiration / styles. https://www.instagram.com/jan.ter.hoeven/

Target Market(s)

average bottle price for this premium red pinot noir would be aroundUS$40. target market are generally urban professionals aged 25 and older with a high degree of interest in pinot noir wine, and who are familiar with New Zealand pinot noir (ie. already know several brands).

Colors
ed252d

Requirements
Must have
• distinctive label, sophisticated look
Nice to have
• classy white paper stock
Should not have
• label must not get too busy... less but high quality and distinctive is more....

```html
<!DOCTYPE html>
<html lang="en">
<head>
<meta charset="utf-8">
<title>WREN – ter Hoeven vineyard label</title>
<link rel="stylesheet" href="https://fonts.googleapis.com/css2?family=Federo&display=swap">
<style>
  :root {
    --paper: #f5ede1;
    --wine-red: #ed252d;
    --wine-red-soft: #f08a8c;
    --wine-red-pale: #f3c9c6;
  }
  html, body {
    margin: 0;
    padding: 0;
    overflow: hidden;
    background: var(--paper);
  }
  .label {
    position: relative;
    width: 1029px;
    height: 1200px;
    background: var(--paper);
    color: var(--wine-red);
    font-family: "Federo", sans-serif;
    overflow: hidden;
  }
  .label__frame {
    position: absolute;
    left: 26px;
    top: 29px;
    width: 968px;
    height: 1143px;
    box-sizing: border-box;
    border: 3px solid var(--wine-red);
    border-radius: 44px;
  }
  .rule {
    position: absolute;
    height: 3px;
    background: var(--wine-red);
  }
  .rule--title-left  { left: 90px;  top: 103px; width: 219px; }
  .rule--title-right { left: 702px; top: 103px; width: 221px; }
  .rule--divider     { left: 276px; top: 1080px; width: 464px; height: 3px; }
  .brand-name {
    position: absolute;
    left: 0;
    right: 0;
    top: 44px;
    margin: 0;
    text-align: center;
    font-size: 104px;
    font-weight: 400;
    line-height: 1;
    letter-spacing: 2px;
  }
  .estate-name {
    position: absolute;
    left: 0;
    right: 0;
    top: 214px;
    margin: 0;
    text-align: center;
    font-size: 56px;
    font-weight: 400;
    line-height: 1;
    letter-spacing: 10px;
  }
  .bird-artwork {
    position: absolute;
    left: 297px;
    top: 290px;
    width: 430px;
    height: 668px;
    border-radius: 46% 46% 40% 40% / 38% 38% 30% 30%;
    background: radial-gradient(ellipse at 45% 40%, var(--wine-red-soft) 0%, var(--wine-red-pale) 60%, var(--paper) 100%);
  }
  .vineyard-name {
    position: absolute;
    left: 0;
    right: 0;
    top: 990px;
    margin: 0;
    text-align: center;
    font-size: 54px;
    font-weight: 400;
    line-height: 1;
  }
  .region {
    position: absolute;
    left: 0;
    right: 0;
    top: 1106px;
    margin: 0;
    text-align: center;
    font-size: 32px;
    font-weight: 400;
    line-height: 1;
  }
</style>
</head>
<body>
  <main class="label">
    <div class="label__frame"></div>

    <div class="rule rule--title-left"></div>
    <h1 class="brand-name">WREN</h1>
    <div class="rule rule--title-right"></div>

    <p class="estate-name">TER HOEVEN</p>

    <div class="bird-artwork" role="img" aria-label="Red engraved illustration of a wren perched on a branch"></div>

    <p class="vineyard-name">ter Hoeven vineyard</p>
    <div class="rule rule--divider"></div>
    <p class="region">Bendigo, Central Otago</p>
  </main>
</body>
</html>
```